Business Card Design For A Renovation Contractor Company

We need a business card for a new company based in Singapore, our company name is "RB Tolvane". We are a renovation contractor that builds designs into reality. We build more of F&B restaurants, retail stores and commercial offices. We work very closely with designers. The final design should communicate to our client that we are a company that you can trust, that will plan and complete your project without giving you a headache. I like my client to remember my company as "RB". The beauty of SIMPLE is important.

Industry/Entity Type

Contractor

Requirements
Nice to have
• Black or Red base

```html
<!DOCTYPE html>
<html lang="en">
<head>
<meta charset="utf-8">
<title>RB Tolvane – Business Cards</title>
<link rel="stylesheet" href="https://fonts.googleapis.com/css2?family=Source+Sans+3:wght@400;600;700&display=swap">
<style>
  :root {
    --ink: #1a1a1a;
    --red: #e0262b;
    --paper: #ffffff;
    --backdrop: #ece8e3;
    --faint: rgba(224, 38, 43, 0.07);
  }
  * { box-sizing: border-box; margin: 0; padding: 0; }
  html, body {
    width: 1200px; height: 720px; overflow: hidden;
    background: var(--backdrop);
    font-family: "Source Sans 3", Arial, sans-serif;
    color: var(--ink);
  }
  .sheet {
    position: relative; width: 1200px; height: 720px;
    display: flex; align-items: center; justify-content: center; gap: 40px;
  }
  .card {
    position: relative; width: 540px; height: 309px;
    background: var(--paper);
    box-shadow: 0 6px 18px rgba(0,0,0,0.12);
    overflow: hidden;
  }

  /* ---------- Front ---------- */
  .brand { position: absolute; left: 42px; top: 34px; width: 300px; }
  .brand-mark { display: flex; align-items: center; gap: 12px; }
  .brand-dot {
    width: 40px; height: 40px; border-radius: 50%;
    background: var(--red);
  }
  .brand-name {
    font-size: 40px; font-weight: 400; letter-spacing: -0.5px;
    color: var(--ink); line-height: 1;
  }
  .tagline {
    margin-top: 6px; padding-top: 3px;
    border-top: 1.5px solid var(--ink);
    font-size: 15px; color: var(--ink); letter-spacing: 0.4px;
  }
  .contact-list {
    position: absolute; left: 42px; top: 158px;
    list-style: none; font-size: 13.5px; color: var(--ink);
  }
  .contact-list li { display: flex; align-items: center; gap: 9px; height: 19px; }
  .contact-list svg { width: 12px; height: 12px; flex: none; }
  .contact-list .address { margin-top: 6px; }
  .edge-bar {
    position: absolute; left: 0; top: 168px; width: 12px; height: 98px;
    background: var(--ink); border-radius: 0 6px 6px 0;
  }
  .holder { position: absolute; right: 30px; top: 40px; text-align: right; }
  .holder-name { font-size: 17px; font-weight: 700; color: var(--ink); line-height: 1.1; }
  .holder-title { font-size: 12px; color: var(--red); }
  .edge-tab {
    position: absolute; right: 0; top: 36px; width: 14px; height: 38px;
    background: var(--red); border-radius: 8px 0 0 8px;
  }

  /* ---------- Back ---------- */
  .back-mark {
    position: absolute; left: 50%; top: 50%;
    width: 230px; height: 230px; margin: -125px 0 0 -115px;
    border-radius: 50%; background: var(--faint);
  }
  .back-brand {
    position: absolute; left: 0; right: 0; top: 96px; text-align: center;
  }
  .back-brand .brand-name { font-size: 64px; }
  .back-brand .tagline {
    display: inline-block; font-size: 21px; margin-top: 8px; padding: 3px 14px 0;
  }
  .web {
    position: absolute; left: 0; right: 0; bottom: 44px; text-align: center;
    font-size: 16px; letter-spacing: 3px; color: var(--ink);
  }
  .web .accent { color: var(--red); }
</style>
</head>
<body>
<main class="sheet">

  <section class="card card-front" aria-label="Business card front">
    <div class="brand">
      <div class="brand-mark">
        <span class="brand-dot" aria-hidden="true"></span>
        <span class="brand-name">RB Tolvane</span>
      </div>
      <p class="tagline">from plan to finished space</p>
    </div>

    <ul class="contact-list">
      <li>
        <svg viewBox="0 0 12 12" aria-hidden="true"><circle cx="6" cy="6" r="6" fill="var(--red)"/><path d="M4 3.2l1.2 1.4-.6.7c.4.9 1.1 1.6 2 2l.7-.6L8.8 8l-.8.9C5.6 8.6 3.4 6.4 3.1 4z" fill="#fff"/></svg>
        123-456-0789
      </li>
      <li>
        <svg viewBox="0 0 12 12" aria-hidden="true"><circle cx="6" cy="6" r="6" fill="var(--red)"/><rect x="4.2" y="2.6" width="3.6" height="6.8" rx="0.6" fill="#fff"/></svg>
        123-456-0789
      </li>
      <li>
        <svg viewBox="0 0 12 12" aria-hidden="true"><circle cx="6" cy="6" r="6" fill="var(--red)"/><rect x="3" y="4" width="6" height="4.2" fill="#fff"/><path d="M3 4l3 2.3L9 4" stroke="var(--red)" stroke-width="0.7" fill="none"/></svg>
        info@rbtolvane.com
      </li>
      <li>
        <svg viewBox="0 0 12 12" aria-hidden="true"><circle cx="6" cy="6" r="6" fill="var(--red)"/><circle cx="6" cy="6" r="3.2" stroke="#fff" stroke-width="0.8" fill="none"/><path d="M2.8 6h6.4M6 2.8c-1.4 1.6-1.4 4.8 0 6.4M6 2.8c1.4 1.6 1.4 4.8 0 6.4" stroke="#fff" stroke-width="0.7" fill="none"/></svg>
        www.rbtolvane.com
      </li>
      <li class="address">Street Name, City Name, State Zip Code</li>
    </ul>

    <span class="edge-bar" aria-hidden="true"></span>

    <div class="holder">
      <p class="holder-name">Your Name</p>
      <p class="holder-title">Title</p>
    </div>
    <span class="edge-tab" aria-hidden="true"></span>
  </section>

  <section class="card card-back" aria-label="Business card back">
    <span class="back-mark" aria-hidden="true"></span>
    <div class="back-brand">
      <span class="brand-name">RB Tolvane</span><br>
      <p class="tagline">from plan to finished space</p>
    </div>
    <p class="web">www.<span class="accent">rbtolvane</span>.com</p>
  </section>

</main>
</body>
</html>
```